Timber Crest Construction Needs business card

Hey we are in need of business card designs. I have upload our logo as a guideline, but free feel to run with it or come up with something unique.
Pls have fun with it and be creative. the name says it all!
i will give some directions after i see a few entries..
Updates
Logo source file has been uploaded..
Hey because of the logo is so colourful already.
Can we have a few submissions with less colour.
Also we are looking for clever/hidden/descriptive business card.

```html
<!DOCTYPE html>
<html lang="en">
<head>
<meta charset="utf-8">
<title>Timber Crest Construction – Business Card</title>
<link rel="stylesheet" href="https://fonts.googleapis.com/css2?family=Arimo:wght@400;700&display=swap">
<style>
  :root {
    --backdrop: #e9e6e1;
    --card: #ffffff;
    --ink: #2b2b2b;
    --brand-grey: #5b6064;
    --rule: #c9c9c9;
    --band-start: #6fdc12;
    --band-end: #8fe24a;
    --faint: #eef1f4;
  }
  * { box-sizing: border-box; margin: 0; padding: 0; }
  html, body { width: 1200px; height: 470px; overflow: hidden; }
  body {
    background: var(--backdrop);
    font-family: "Arimo", Arial, sans-serif;
    color: var(--ink);
    position: relative;
  }
  .card {
    position: absolute;
    top: 70px;
    width: 560px;
    height: 330px;
    background: var(--card);
    box-shadow: 0 6px 18px rgba(0,0,0,.18);
    overflow: hidden;
  }
  .card--front { left: 25px; }
  .card--back { left: 615px; }

  .brand {
    position: absolute;
    left: 36px;
    top: 118px;
    width: 230px;
    display: flex;
    align-items: center;
    gap: 10px;
  }
  .brand__mark { width: 18px; height: 18px; background: var(--brand-grey); flex: none; }
  .brand__name {
    font-weight: 700;
    font-size: 22px;
    line-height: 1.1;
    color: var(--brand-grey);
  }
  .divider {
    position: absolute;
    left: 278px;
    top: 34px;
    width: 1px;
    height: 150px;
    background: var(--rule);
  }
  .contact {
    position: absolute;
    left: 300px;
    top: 34px;
    font-size: 14px;
    line-height: 1.35;
  }
  .contact__address { margin-bottom: 12px; }
  .contact__list { list-style: none; }
  .contact__list li { display: flex; align-items: center; gap: 6px; height: 22px; white-space: nowrap; }
  .contact__list svg { width: 12px; height: 12px; flex: none; }

  .footer-band {
    position: absolute;
    left: 0;
    bottom: 0;
    width: 560px;
    height: 80px;
    background: linear-gradient(90deg, var(--band-start), var(--band-end));
  }
  .holder {
    position: absolute;
    left: 50px;
    bottom: 28px;
    font-weight: 700;
    font-size: 19px;
    color: #fff;
  }

  .back-brand {
    position: absolute;
    left: 0; right: 0;
    top: 110px;
    text-align: center;
  }
  .back-brand__name {
    font-weight: 700;
    font-size: 34px;
    color: var(--brand-grey);
  }
  .back-brand__web {
    margin-top: 10px;
    font-size: 18px;
    color: var(--ink);
  }
  .back-rules { position: absolute; left: 0; bottom: 22px; width: 560px; height: 20px; }
</style>
</head>
<body>
  <section class="card card--front" aria-label="Business card front">
    <div class="footer-band" role="img" aria-label="Decorative flowing wave band along the bottom of the card"></div>

    <div class="brand">
      <span class="brand__mark"></span>
      <span class="brand__name">Timber Crest Construction</span>
    </div>

    <div class="divider"></div>

    <div class="contact">
      <p class="contact__address">Street Name City Name<br>State Zipcode</p>
      <ul class="contact__list">
        <li><svg viewBox="0 0 12 12"><circle cx="6" cy="6" r="5.5" fill="none" stroke="var(--ink)"/><path d="M4 3.5 L5 3 L6 5 L5.3 5.6 Q6 7 6.8 7.4 L7.5 6.8 L9 8 L8.5 9 Q5 9 3.6 4.8 Z" fill="var(--ink)"/></svg>0400 555 318</li>
        <li><svg viewBox="0 0 12 12"><circle cx="6" cy="6" r="5.5" fill="none" stroke="var(--ink)"/><path d="M4 3.5 L5 3 L6 5 L5.3 5.6 Q6 7 6.8 7.4 L7.5 6.8 L9 8 L8.5 9 Q5 9 3.6 4.8 Z" fill="var(--ink)"/></svg>0400 555 318</li>
        <li><svg viewBox="0 0 12 12"><rect x="1" y="3" width="10" height="7" fill="var(--ink)"/><path d="M1 3 L6 7 L11 3" fill="none" stroke="#fff"/></svg>hello@timbercrestbuild.com</li>
        <li><svg viewBox="0 0 12 12"><circle cx="6" cy="6" r="5" fill="none" stroke="var(--ink)" stroke-width="1.3"/><ellipse cx="6" cy="6" rx="2" ry="5" fill="none" stroke="var(--ink)"/><path d="M1 6 H11" stroke="var(--ink)"/></svg>www.timbercrestbuild.com</li>
      </ul>
    </div>

    <p class="holder">Your Name, Title</p>
  </section>

  <section class="card card--back" aria-label="Business card back">
    <div class="back-brand">
      <p class="back-brand__name">Timber Crest Construction</p>
      <p class="back-brand__web">www.timbercrestbuild.com</p>
    </div>
    <svg class="back-rules" viewBox="0 0 560 20" aria-hidden="true">
      <rect x="0" y="2" width="560" height="4" fill="var(--faint)"/>
      <rect x="0" y="12" width="560" height="6" fill="var(--faint)"/>
    </svg>
  </section>
</body>
</html>
```